Executive Coaching and Spiritual Development Company needs a business card design.

We need a business card design for our company. We already have a logo that was created through Brightloom that we will submit and would like to see this work on black, blue and white backgrounds. Our personal information should be included as well. The design should communicate trust, spirituality, support and partnership.

Industry/Entity Type

Business

Colors
0255a3
33a6d7
ffffff
000000
474747

Requirements
Nice to have
• The colors offered here are just ideas--we are open to other suggestions, too.

```html
<!DOCTYPE html>
<html lang="en">
<head>
<meta charset="utf-8">
<title>Tidewell Business Card</title>
<link rel="stylesheet" href="https://fonts.googleapis.com/css2?family=Source+Sans+3:wght@400;600&display=swap">
<style>
  :root {
    --brand-blue: #0255a3;
    --ink-blue: #2b5aa8;
    --ink-dark: #16202a;
    --ink-grey: #474747;
    --paper: #ffffff;
    --backdrop: #e9e6e1;
    --icon: #1a1a1a;
  }
  * { margin: 0; padding: 0; box-sizing: border-box; }
  html, body {
    width: 1200px; height: 1000px; overflow: hidden;
    background: var(--backdrop);
    font-family: "Source Sans 3", sans-serif;
  }
  .sheet {
    width: 1200px; height: 1000px;
    display: flex; flex-direction: column; align-items: center; justify-content: center;
    gap: 36px;
  }
  .card {
    position: relative;
    width: 780px; height: 446px;
    box-shadow: 0 6px 18px rgba(0,0,0,0.18);
  }
  /* Front */
  .card-front { background: var(--brand-blue); }
  .front-brand {
    position: absolute; left: 90px; top: 50%; transform: translateY(-50%);
    display: flex; align-items: center; gap: 26px;
  }
  .front-brand .brand-circle {
    width: 150px; height: 150px; border-radius: 50%;
    border: 3px solid var(--paper);
  }
  .front-brand .brand-name {
    font-size: 92px; font-weight: 600; color: var(--paper); letter-spacing: 1px;
  }
  /* Back */
  .card-back { background: var(--paper); }
  .holder {
    position: absolute; left: 40px; top: 30px;
  }
  .holder-name {
    font-size: 25px; font-weight: 400; color: var(--ink-blue); letter-spacing: 0.5px;
    text-transform: uppercase; line-height: 1.1;
  }
  .holder-role { font-size: 17px; color: var(--ink-grey); margin-top: 2px; }
  .back-brand {
    position: absolute; left: 355px; top: 22px;
    display: flex; align-items: center; gap: 12px;
  }
  .back-brand .brand-circle {
    width: 88px; height: 88px; border-radius: 50%;
    border: 2px solid var(--ink-dark);
  }
  .back-brand .brand-name {
    font-size: 52px; font-weight: 600; color: var(--ink-dark); letter-spacing: 0.5px;
  }
  .back-emblem {
    position: absolute; left: 30px; top: 206px;
    width: 212px; height: 212px; border-radius: 50%;
    border: 3px solid var(--ink-dark);
  }
  .contact-list {
    position: absolute; right: 66px; top: 198px;
    list-style: none; text-align: right;
  }
  .contact-list li {
    display: flex; align-items: center; justify-content: flex-end; gap: 14px;
    font-size: 19px; color: var(--ink-blue); height: 30px;
  }
  .contact-list svg { width: 20px; height: 20px; fill: var(--icon); flex: none; }
</style>
</head>
<body>
<main class="sheet">
  <section class="card card-front" aria-label="Card front">
    <div class="front-brand">
      <span class="brand-circle"></span>
      <span class="brand-name">Tidewell</span>
    </div>
  </section>

  <section class="card card-back" aria-label="Card back">
    <div class="holder">
      <p class="holder-name">Mara Quell</p>
      <p class="holder-role">General Manager</p>
    </div>
    <div class="back-brand">
      <span class="brand-circle"></span>
      <span class="brand-name">Tidewell</span>
    </div>
    <span class="back-emblem"></span>
    <ul class="contact-list">
      <li>+010 555 014 277
        <svg viewBox="0 0 24 24" aria-hidden="true"><path d="M6.6 10.8a15.1 15.1 0 0 0 6.6 6.6l2.2-2.2c.3-.3.7-.4 1-.2 1.1.4 2.3.6 3.6.6.6 0 1 .4 1 1V20c0 .6-.4 1-1 1C10.6 21 3 13.4 3 4c0-.6.4-1 1-1h3.5c.6 0 1 .4 1 1 0 1.3.2 2.5.6 3.6.1.3 0 .7-.2 1z"/></svg>
      </li>
      <li>+555 201 483 9126
        <svg viewBox="0 0 24 24" aria-hidden="true"><path d="M7 1h10a2 2 0 0 1 2 2v18a2 2 0 0 1-2 2H7a2 2 0 0 1-2-2V3a2 2 0 0 1 2-2zm0 3v14h10V4zm5 15.2a1 1 0 1 0 0 2 1 1 0 0 0 0-2z"/></svg>
      </li>
      <li>+555 201 483 9127
        <svg viewBox="0 0 24 24" aria-hidden="true"><path d="M6 2h9l3 3v4H6zM4 10h16a2 2 0 0 1 2 2v6h-4v4H6v-4H2v-6a2 2 0 0 1 2-2zm4 6v4h8v-4z"/></svg>
      </li>
      <li>mara@tidewell.com
        <svg viewBox="0 0 24 24" aria-hidden="true"><path d="M2 5h20v14H2zm2 2v.5l8 5 8-5V7z"/></svg>
      </li>
      <li>www.tidewell.com
        <svg viewBox="0 0 24 24" aria-hidden="true"><path d="M12 2a10 10 0 1 0 0 20 10 10 0 0 0 0-20zm-1 17.9A8 8 0 0 1 4.2 10L9 14.8v1a2 2 0 0 0 2 2zm6.9-2.5A2 2 0 0 0 16 16h-1v-3a1 1 0 0 0-1-1H8v-2h2a1 1 0 0 0 1-1V7h2a2 2 0 0 0 2-2v-.4a8 8 0 0 1 2.9 12.8z"/></svg>
      </li>
    </ul>
  </section>
</main>
</body>
</html>
```